Stylish new business card needed!

Hello everyone! I am in need of a new business card design for an alarm company here in Hurricane WV. I have all fonts, color codes and logos provided for you use! We are a young company and like the style of a clean sleek looking business card. Would like it double sided, one side holding the logo and the other with your design!
Target Market(s)
The people that are looking for the newest tech for home automation and security
Industry/Entity Type
Alarm services; Home automation
Contact Information for Business Card
Name of person; position (Sales; Installer); Phone Number (555.418.7260); Employee cell Number; Website (www.GuardedByVelk.example); Employee Email; Double sided
Look and feel
Each slider illustrates characteristics of the customer's brand and the style your logo design should communicate.

```html
<!DOCTYPE html>
<html lang="en">
<head>
<meta charset="utf-8">
<title>Guarded By Velk — Business Card</title>
<link rel="stylesheet" href="https://fonts.googleapis.com/css2?family=Montserrat:wght@700;800;900&family=Arimo:wght@400;700&display=swap">
<style>
  :root {
    --stage: #262626;
    --card: #222226;
    --card-edge: #f08a45;
    --orange: #f58b47;
    --grey: #9a9a9a;
    --white: #ffffff;
    --pattern-dark: #1d1d21;
    --pattern-light: #3a3a3f;
  }
  * { box-sizing: border-box; margin: 0; padding: 0; }
  html, body { width: 1200px; height: 780px; overflow: hidden; }
  body { background: var(--stage); position: relative; font-family: "Arimo", Arial, sans-serif; }

  .card {
    position: absolute;
    width: 560px; height: 320px;
    background: var(--card);
    border-radius: 20px;
    border-bottom: 4px solid var(--card-edge);
    border-right: 2px solid var(--card-edge);
    box-shadow: 0 14px 30px rgba(0,0,0,.55);
    overflow: hidden;
  }
  .card--back { left: 250px; top: 50px; }
  .card--front { left: 390px; top: 410px; }

  .back-pattern {
    position: absolute; inset: 0;
    background: linear-gradient(160deg, var(--pattern-light) 0%, var(--pattern-dark) 45%, var(--pattern-light) 75%, var(--pattern-dark) 100%);
  }
  .back-mark {
    position: absolute; right: 70px; top: 150px;
    font-family: "Montserrat", sans-serif; font-weight: 800;
    font-size: 13px; letter-spacing: 1px; color: var(--orange);
  }

  .brand {
    position: absolute; left: 34px; top: 120px;
    font-family: "Montserrat", sans-serif; font-weight: 800;
    color: var(--orange); line-height: 1.05; letter-spacing: 1px;
  }
  .brand__line { display: block; font-size: 20px; }
  .brand__name { display: block; font-size: 58px; letter-spacing: 2px; }

  .divider {
    position: absolute; left: 272px; top: 36px;
    width: 2px; height: 190px; background: var(--white);
  }

  .person { position: absolute; left: 296px; top: 40px; }
  .person__name {
    font-family: "Montserrat", sans-serif; font-weight: 900; font-size: 26px;
    color: var(--grey); white-space: nowrap;
  }
  .person__name .first { color: var(--orange); }
  .person__role {
    font-family: "Arimo", sans-serif; font-weight: 700; font-size: 14px;
    color: var(--white); margin-top: 2px; margin-left: 14px;
  }

  .contacts { position: absolute; left: 310px; top: 118px; list-style: none; }
  .contacts li {
    display: flex; align-items: center; gap: 9px;
    color: var(--white); font-size: 13.5px; height: 22px; white-space: nowrap;
  }
  .contacts svg { width: 14px; height: 14px; flex: none; }

  .bands { position: absolute; left: 0; bottom: 0; width: 560px; height: 320px; }
</style>
</head>
<body>

  <section class="card card--back" aria-label="Card back">
    <div class="back-pattern" role="img" aria-label="Repeating brand-name pattern in dark tone on tone"></div>
    <div class="back-mark">GUARDED BY VELK</div>
  </section>

  <section class="card card--front" aria-label="Card front">
    <div class="brand">
      <span class="brand__line">GUARDED BY</span>
      <span class="brand__name">VELK</span>
    </div>

    <div class="divider"></div>

    <div class="person">
      <div class="person__name"><span class="first">Marta</span> Kovalik</div>
      <div class="person__role">Sales; Installer</div>
    </div>

    <ul class="contacts">
      <li>
        <svg viewBox="0 0 16 16"><path fill="#f58b47" d="M3 1l3 3-1.5 2a9 9 0 0 0 5.5 5.5L12 10l3 3-2 2C7 15 1 9 1 3z"/></svg>
        555.418.7260
      </li>
      <li>
        <svg viewBox="0 0 16 16"><rect x="4" y="1" width="8" height="14" rx="1.5" fill="none" stroke="#ffffff" stroke-width="1.5"/></svg>
        555.602.1934
      </li>
      <li>
        <svg viewBox="0 0 16 16"><circle cx="8" cy="8" r="6.5" fill="#f58b47"/><path d="M1.5 8h13M8 1.5c-3 3.5-3 9.5 0 13M8 1.5c3 3.5 3 9.5 0 13" stroke="#222226" stroke-width="1" fill="none"/></svg>
        www.GuardedByVelk.example
      </li>
      <li>
        <svg viewBox="0 0 16 16"><rect x="1" y="4" width="14" height="10" rx="1" fill="#f58b47"/><path d="M1 4l7 6 7-6" stroke="#222226" stroke-width="1.2" fill="none"/></svg>
        info@GuardedByVelk.example
      </li>
    </ul>

    <svg class="bands" viewBox="0 0 560 320" aria-hidden="true">
      <path d="M0 274 L300 274 L322 256 L560 256 L560 282 L340 282 Q326 282 318 290 L0 290 Z" fill="none"/>
      <path d="M292 256 L560 232 L560 254 L342 254 Q326 256 318 262 Z" fill="var(--grey)"/>
      <path d="M0 300 L0 278 L300 258 Q316 256 330 258 L300 270 Z" fill="var(--orange)"/>
    </svg>
  </section>

</body>
</html>
```